Flyer design for retail store owners

i would need to have a flyer design for my retail shop customers to show that I am a mailbox store that has all major shipping vendors to for their shipping needs. Ensuring that they can take advantage of opening a house account at the store and billed monthly, word document has all the details. Please use stock images for the notary public, passport photos, mailbox brass pictures of my actual mailboxes are listed in the pictures. I need to make it POP and WOW these retail store owners as I am using it to advertise the business

```html
<!DOCTYPE html>
<html lang="en">
<head>
<meta charset="utf-8">
<title>Mailbox Rental Flyer</title>
<link rel="stylesheet" href="https://fonts.googleapis.com/css2?family=Fjalla+One&family=Lato:ital,wght@0,400;0,700;0,900;1,400;1,700&display=swap">
<style>
:root{
  --stage:#e59a7f;
  --paper:#f3f2f0;
  --navy:#25235e;
  --red:#d7262e;
  --white:#ffffff;
  --ink:#2b2b33;
}
*{margin:0;padding:0;box-sizing:border-box}
html,body{width:1200px;height:959px;overflow:hidden;background:var(--stage)}
.canvas{position:relative;width:1200px;height:959px}
.page{position:absolute;top:100px;width:540px;height:760px;background:var(--paper);overflow:hidden;box-shadow:0 18px 40px rgba(120,50,30,.25)}
.page--front{left:40px}
.page--back{left:620px}
.layer{position:absolute;left:0;top:0}
.headline{position:absolute;left:40px;top:416px;font-family:"Fjalla One",sans-serif;font-size:50px;line-height:1;color:var(--navy);letter-spacing:-.5px}
.headline-rule{position:absolute;left:40px;top:472px;width:330px;height:3px;background:var(--red)}
.intro{position:absolute;left:40px;top:484px;width:470px;font-family:Lato,sans-serif;font-size:12px;line-height:1.35;color:var(--ink)}
.ribbon{position:absolute;left:250px;top:604px;width:290px;height:28px;background:var(--navy);clip-path:polygon(0 0,100% 0,100% 100%,22px 100%);color:var(--white);font-family:Lato,sans-serif;font-style:italic;font-size:13px;line-height:28px;padding-left:38px}
.stripe{position:absolute;left:0;top:640px;width:540px;height:4px;background:var(--red)}
.footer-block{position:absolute;left:0;top:650px;width:540px;height:110px;background:var(--red);padding:8px 40px 0;color:var(--white);font-family:Lato,sans-serif;font-size:11.6px;line-height:1.33}
.promo-badge{position:absolute;left:390px;top:262px;width:140px;height:140px;border-radius:50%;background:var(--white);border:7px solid var(--red);text-align:center;color:var(--navy);font-family:Lato,sans-serif;font-weight:900}
.promo-badge .tag{display:block;margin-top:12px;font-size:10px;line-height:1.1}
.promo-badge .price{display:block;margin-top:4px;font-family:"Fjalla One",sans-serif;font-weight:400;font-size:42px;line-height:1.05}
.promo-badge .terms{display:block;margin-top:2px;font-size:9.5px;line-height:1.1}
.back-heading{position:absolute;left:36px;top:440px;font-family:Lato,sans-serif;font-weight:700;font-size:19px;color:var(--navy);letter-spacing:-.3px}
.back-intro{position:absolute;left:36px;top:467px;width:470px;font-family:Lato,sans-serif;font-style:italic;font-size:11.5px;line-height:1.35;color:var(--ink)}
.deals-title{position:absolute;left:36px;top:536px;font-family:"Fjalla One",sans-serif;font-size:20px;color:var(--navy)}
.deal-list{position:absolute;left:36px;top:568px;width:470px;list-style:none;font-family:Lato,sans-serif;font-size:11.5px;line-height:1.3;color:var(--ink)}
.deal-list li{position:relative;padding-left:18px;margin-bottom:3px}
.deal-list svg{position:absolute;left:0;top:1px}
.footer-band{position:absolute;left:0;top:722px;width:540px;height:38px;background:var(--red)}
</style>
</head>
<body>
<main class="canvas">

  <section class="page page--front">
    <svg class="layer" width="540" height="460" viewBox="0 0 540 460">
      <defs>
        <linearGradient id="roomTone" x1="0" y1="0" x2="1" y2="1">
          <stop offset="0" stop-color="#f4f1ec"/><stop offset="1" stop-color="#ddd6cf"/>
        </linearGradient>
        <linearGradient id="brassTone" x1="0" y1="0" x2="1" y2="1">
          <stop offset="0" stop-color="#d9bd84"/><stop offset="1" stop-color="#b08c4e"/>
        </linearGradient>
      </defs>
      <rect class="room-photo" width="540" height="460" fill="url(#roomTone)" role="img" aria-label="Soft-focus bright office interior"/>
      <polygon class="navy-corner" points="360,0 540,0 540,240" fill="var(--navy)"/>
      <rect x="0" y="0" width="540" height="5" fill="var(--red)"/>
      <rect class="mailbox-photo" x="240" y="30" width="250" height="310" rx="4" fill="url(#brassTone)" role="img" aria-label="Brass mailbox cabinet with rows of small locking doors"/>
      <path class="red-swoosh" d="M0,320 Q260,420 540,330 L540,460 L0,460 Z" fill="var(--red)"/>
      <path class="white-swoosh" d="M0,345 Q260,450 540,360 L540,460 L0,460 Z" fill="var(--paper)"/>
      <g class="pointers" fill="var(--navy)">
        <polygon points="180,115 290,140 192,150"/>
        <polygon points="200,225 300,190 208,247"/>
        <polygon points="240,305 310,250 252,325"/>
      </g>
      <g class="service-circles">
        <circle cx="128" cy="110" r="64" fill="#7a2b3a" stroke="var(--navy)" stroke-width="5" role="img" aria-label="Two passports with boarding passes"/>
        <circle cx="158" cy="225" r="50" fill="#9a7e6a" stroke="var(--navy)" stroke-width="5" role="img" aria-label="Wax seal stamp on a rolled document"/>
        <circle cx="212" cy="312" r="46" fill="#8c8f8e" stroke="var(--navy)" stroke-width="5" role="img" aria-label="Stack of stamped envelopes in a mailbox"/>
      </g>
    </svg>

    <div class="promo-badge">
      <span class="tag">exclusive<br>promo deal!</span>
      <span class="price">$12</span>
      <span class="terms">a month for 6-12<br>months leases!</span>
    </div>

    <h1 class="headline">Renting a mail box</h1>
    <div class="headline-rule"></div>
    <p class="intro">Renting a mail box is one of the most efficient and cost saving methods for receiving your mail and packages. Instead of having to worry about private security, weather conditions, sorting and deliveries; all you have to do is pick-up your mail from our secured facility each day except Sundays. You will get a notification when mail arrives whether envelope or package, it will be scanned in daily which other mailbox stores do not offer! We offer onsite Notary Public with no appointments and onsite Passport Photos and can ship out same day.</p>

    <div class="ribbon">Take advantage of this limited time offer!</div>
    <div class="stripe"></div>

    <div class="footer-block">At Swift Parcel Hub, our goal is to make your shipping experience as convenient as possible. Whether you are shipping packages, documents, or packages, we are here to help. If you want to track your package or estimate the price of your package, it is easy and we are ready to handle all of your postal services! Get also the services you need; printing, copying, and stop in to purchase postage or shipping materials. Service point for SkyFreight, ParcelWay, National Post, and GlobeXpress.</div>
  </section>

  <section class="page page--back">
    <svg class="layer" width="540" height="440" viewBox="0 0 540 440">
      <defs>
        <linearGradient id="sealTone" x1="0" y1="0" x2="1" y2="1">
          <stop offset="0" stop-color="#bdb6b3"/><stop offset="1" stop-color="#ece8e4"/>
        </linearGradient>
        <linearGradient id="boxesTone" x1="0" y1="0" x2="0" y2="1">
          <stop offset="0" stop-color="#7d5a3a"/><stop offset=".6" stop-color="#c2a98a"/><stop offset="1" stop-color="#f3f2f0"/>
        </linearGradient>
      </defs>
      <rect x="0" y="0" width="540" height="5" fill="var(--red)"/>
      <rect class="mailbox-row-photo" x="0" y="310" width="540" height="120" fill="url(#boxesTone)" role="img" aria-label="Blurred wall of brass mailboxes"/>
      <path class="seal-photo" d="M0,5 L540,5 L540,300 Q270,380 0,300 Z" fill="url(#sealTone)" role="img" aria-label="Wooden wax seal stamp resting on a sealed scroll"/>
      <path class="red-swoosh" d="M0,300 Q270,380 540,300 L540,328 Q270,415 0,328 Z" fill="var(--red)"/>
      <circle class="envelopes-photo" cx="560" cy="30" r="165" fill="#9b8f7c" role="img" aria-label="Mailbox number plate with stamped envelopes"/>
      <path d="M395,30 A165,165 0 0 0 560,195" fill="none" stroke="#e8b9a8" stroke-width="4"/>
      <circle class="passport-photo" cx="448" cy="262" r="78" fill="#f7f4f1" stroke="var(--red)" stroke-width="9"/>
      <rect x="402" y="222" width="92" height="82" rx="6" fill="#7a2b3a" role="img" aria-label="Red and blue passports with boarding passes"/>
    </svg>

    <h2 class="back-heading">Now renting mailboxes on Maple Ridge Commons.</h2>
    <p class="back-intro">We are offering all Maple Ridge Commons owners/employees an exclusive promo deal! $12 a month for 6-12 months leases! You get a mailbox in the shop, a book of stamps(20 count), 3 notarizations by appointment, 100 copies of black and white, and 100 copies of color. Please see associate for sign up!</p>

    <h3 class="deals-title">CHECK OUT THESE OTHER DEALS!</h3>
    <ul class="deal-list">
      <li><svg width="12" height="12" viewBox="0 0 12 12"><circle cx="6" cy="6" r="5" fill="none" stroke="var(--red)" stroke-width="1.4"/><path d="M3,6 L5.3,8.2 L10.5,2" fill="none" stroke="var(--red)" stroke-width="2"/></svg>As a retail owner, you know how important it is to keep your customers coming back - you will get 20% discount for printing services.</li>
      <li><svg width="12" height="12" viewBox="0 0 12 12"><circle cx="6" cy="6" r="5" fill="none" stroke="var(--red)" stroke-width="1.4"/><path d="M3,6 L5.3,8.2 L10.5,2" fill="none" stroke="var(--red)" stroke-width="2"/></svg>We duplicate keys for $2/each, our regular price charge is $4/each. Save up to 50%! Lamination is also discounted at 10% off.</li>
      <li><svg width="12" height="12" viewBox="0 0 12 12"><circle cx="6" cy="6" r="5" fill="none" stroke="var(--red)" stroke-width="1.4"/><path d="M3,6 L5.3,8.2 L10.5,2" fill="none" stroke="var(--red)" stroke-width="2"/></svg>10% off retail supplies ... must be minimum of 10$</li>
      <li><svg width="12" height="12" viewBox="0 0 12 12"><circle cx="6" cy="6" r="5" fill="none" stroke="var(--red)" stroke-width="1.4"/><path d="M3,6 L5.3,8.2 L10.5,2" fill="none" stroke="var(--red)" stroke-width="2"/></svg>For house accounts -a 5% discount will be deducted monthly of billing change to invoicing PLUS</li>
      <li><svg width="12" height="12" viewBox="0 0 12 12"><circle cx="6" cy="6" r="5" fill="none" stroke="var(--red)" stroke-width="1.4"/><path d="M3,6 L5.3,8.2 L10.5,2" fill="none" stroke="var(--red)" stroke-width="2"/></svg>we're giving another 5% of the discount if you upgrade and sign up for mailbox. Great right?</li>
    </ul>

    <div class="footer-band"></div>
  </section>

</main>
</body>
</html>
```